Smart Routing SaaS needs a magic web design

We need a web design that focuses in the UX and conveys the idea of doing magic through our software. The company name is Brantiq and it is a word game about wow and slip... we are a software as a service B2B that helps companies automate dispatches and routes for their delivery guys to deliver goods to the customers. Think of it as an zephyr software applicable to your own fleet or third party fleets that can be used for example in a supermarket. That way the final user (buyer of the supermarket) knows where the parcel is, if it is leaving the store, if it is on its way, how long will it take to arrive, who is the delivery guy, etc... Brantiq's symbol is an owl. Think of it as the movie The Lanternkeep: Autumn's Oath, Queen Odalie had an owl mask and the ice owl who was her eyes on the field... that is the idea I want to convey through this software. It is the eyes for the business and the eyes for the final user. The software is comprised of a web platform (for the business with the fleet to manage) and the driver's application. The final customer receives the real time tracking information through SMS and email. The design should communicate magic through the use of the software... You can see some info on the existing webpage... which is very cold and dull... no life in it brantiq.example.. Use of gifs is desirable.

Text that can be used on the cover to convey main idea:

High end technology
We take care of your delivery management

The software that brings visibility and smartness to your deliveries through automated dispatches and smart routings
Our expertise: A Delightful Customer Experience of Deliveries

Target Market(s)

Professionals and businesses of all types with a delivery of any kind (supermarkets, pharmacies, restaurants, moving services, fleets, home services, deliveries, supply chain, field sales...)
Please look at competition webpages:
www.pathkit7.example
www.movra.example
www.trekly.example
vantacor.example
quickbarn.example
zephyr dash

Industry/Entity Type

Business Software

Coding

Coded - Design and coding required

Number of Pages Required

5+ page

Font styles to use
Other font styles liked:
• Modulus and Trade Gothic Ltd

Requirements
Must have
• MUST HAVE A D3JS LIKE:
• http://grafnode.example/jterran/5518302
• http://jterran.codepages.example/d3/talk/20111116/force-collapsible.html
• https://plinthware.example/hugo/fisheye/
• http://movingcharts.example/lab/d3-tree/
• A great magic capturing Homepage that conveys the main idea of what we are. A software that will help you manage your people on field who are getting something to the end customer (who will be aware of the live parcel status through SMS/ email notifications), we live in the cloud... no need of implementation fees, there is a free demo. Right now the webpage has an animation. Maybe a picture with a video on it could be something nice, or something that moves... take a look at zephyr dash. The main idea of the page should send the idea of something magic... use the owl... something that flies.
• The page must have gifs here and there... never stop the idea of a swift magic going on... efficiency on the logistics management of the company... happy customers.
• Parallax... I love parallax.
Nice to have
• The webpage may be telling a story... first what are we and what we do... how it works, who is our market, the benefits, hard facts on efficiency... please take a look at the current webpage www.brantiq.example to get more info but make it beautiful.
• A phrase here and there of why they need our service
Should not have
• I want to change the current idea of the webpage that the software aims only to manage fleets for home delivery... we are NOT a home delivery only management system. We can make any company's logistics "fly".
• I dont want to see dullness in the webpage, I am looking for a soul.

```html
<!DOCTYPE html>
<html lang="en">
<head>
<meta charset="utf-8">
<title>Brantiq – About</title>
<link href="https://fonts.googleapis.com/css2?family=Roboto:wght@300;400;500;700&display=swap" rel="stylesheet">
<style>
:root{
  --brand:#14a9c6;
  --brand-dark:#0f93ad;
  --ink:#555a5e;
  --ink-soft:#6d7276;
  --heading:#4b5054;
  --nav:#6a6f73;
  --footer:#2a2a2a;
  --footer-bottom:#1c1c1c;
  --footer-text:#c9c9c9;
  --white:#ffffff;
}
*{margin:0;padding:0;box-sizing:border-box}
html,body{width:1200px;height:1200px;overflow:hidden;background:var(--white)}
body{position:relative;font-family:'Roboto',sans-serif;color:var(--ink)}
.top-rule{position:absolute;left:0;top:0;width:1200px;height:2px;background:var(--brand)}
.site-header{position:absolute;left:0;top:2px;width:1200px;height:110px}
.brand{position:absolute;left:99px;top:40px}
.brand-name{font-size:30px;font-weight:500;color:var(--heading);letter-spacing:.5px;line-height:1}
.main-nav{position:absolute;top:50px;left:551px;display:flex}
.main-nav a{font-size:14.5px;color:var(--nav);text-decoration:none;text-transform:uppercase;margin-right:42px;font-weight:300}
.main-nav a:last-child{margin-right:0}
.main-nav a.active{color:var(--brand)}
.hero{position:absolute;left:0;top:112px;width:1200px;height:310px;overflow:hidden;
  background:linear-gradient(100deg,#15151c 0%,#3b3f5a 10%,#6b6d8c 25%,#4f6b95 42%,#3f7fb0 60%,#5c9ec9 78%,#2d6fa4 100%)}
.hero::after{content:"";position:absolute;inset:0;background:radial-gradient(ellipse at 75% 40%,rgba(160,210,235,.35),transparent 55%)}
.hero-title{position:absolute;left:0;width:1200px;text-align:center;color:var(--white);font-weight:700;z-index:2}
.hero-title.main{top:106px;font-size:44px}
.hero-title.sub{top:165px;font-size:35px;font-weight:500}
.hero-arrow{position:absolute;top:134px;z-index:2}
.hero-arrow.prev{left:27px}
.hero-arrow.next{left:1130px}
.hero-shadow{position:absolute;left:60px;top:422px;width:1080px;height:24px;background:radial-gradient(ellipse at 50% 0%,rgba(0,0,0,.12),transparent 70%)}
.device-showcase{position:absolute;left:97px;top:474px;width:428px;height:332px;border-radius:10px;
  background:linear-gradient(160deg,#e9eef2 0%,#cfdbe4 45%,#2d6aa6 75%,#1c1c1e 100%)}
.about{position:absolute;left:589px;top:474px;width:516px}
.about h2{font-size:31px;font-weight:400;color:var(--heading);margin-left:2px;letter-spacing:.2px}
.about h2 span{color:var(--brand)}
.about .lead{margin-top:19px;font-size:15.8px;line-height:22px;color:var(--ink-soft);font-weight:400}
.about p.body{margin-top:12px;font-size:12.2px;line-height:21.4px;color:#7a7e82;font-weight:300}
.about p.body + p.body{margin-top:10px}
.tagline{position:absolute;left:0;top:852px;width:1200px;text-align:center;font-size:36px;font-weight:400;color:var(--brand)}
.tagline strong{font-weight:700;color:var(--brand-dark)}
.site-footer{position:absolute;left:0;top:937px;width:1200px;height:200px;background:var(--footer)}
.footer-col{position:absolute;top:44px}
.footer-col h3{font-size:17.5px;font-weight:400;color:var(--white);text-transform:uppercase;margin-bottom:12px}
.footer-col li{list-style:none;font-size:12.3px;line-height:21.4px;color:var(--footer-text)}
.col-company{left:102px}
.col-community{left:264px}
.col-follow{left:461px}
.col-contact{left:639px;width:220px}
.col-newsletter{left:893px}
.newsletter-input{position:absolute;left:894px;top:85px;width:207px;height:42px;background:#323232;border:1px solid #3a3a3a;color:#8a8a8a;font-style:italic;font-size:11.5px;padding:13px 14px}
.newsletter-btn{position:absolute;left:1020px;top:140px;width:81px;height:30px;background:var(--brand);border-radius:3px;color:var(--white);font-size:12.5px;text-align:center;line-height:30px}
.footer-bottom{position:absolute;left:0;top:1137px;width:1200px;height:63px;background:var(--footer-bottom);color:#e6e6e6;font-size:12.5px;text-align:center;line-height:63px}
</style>
</head>
<body>
<div class="top-rule"></div>
<header class="site-header">
  <div class="brand"><span class="brand-name">Brantiq</span></div>
  <nav class="main-nav">
    <a href="#">Home</a><a href="#">Platform</a><a href="#" class="active">About</a><a href="#">Contact</a><a href="#">Register</a><a href="#">Login</a>
  </nav>
</header>

<section class="hero" role="img" aria-label="City skyline at dusk overlaid with a glowing network of connected delivery points">
  <h1 class="hero-title main">ABOUT&nbsp; US</h1>
  <p class="hero-title sub">MANAGER OF YOUR DELIVERIES</p>
  <svg class="hero-arrow prev" width="36" height="36" viewBox="0 0 36 36" aria-hidden="true"><circle cx="18" cy="18" r="16.5" fill="none" stroke="#cfd6dc" stroke-width="2"/><path d="M20.5 11 L13.5 18 L20.5 25" fill="none" stroke="#cfd6dc" stroke-width="2"/></svg>
  <svg class="hero-arrow next" width="36" height="36" viewBox="0 0 36 36" aria-hidden="true"><circle cx="18" cy="18" r="16.5" fill="none" stroke="#cfd6dc" stroke-width="2"/><path d="M15.5 11 L22.5 18 L15.5 25" fill="none" stroke="#cfd6dc" stroke-width="2"/></svg>
</section>
<div class="hero-shadow"></div>

<div class="device-showcase" role="img" aria-label="Desktop monitor, tablet and phone showing the Brantiq dispatch dashboard, route map and driver login"></div>

<section class="about">
  <h2>ABOUT OUR <span>BRANTIQ</span></h2>
  <p class="lead">Brantiq was founded with the idea that everyone should have access to a world class technology for delivery management.</p>
  <p class="body">E-commerce is turbo growing all over the world. Big and small businesses are more and more in need of quality fleets to take care of their deliveries. Businesses are relying on third party services to complete the last part of the shopping service to their clients. Until now, the delivery process has been done in the dark. The majority of businesses and customers don't know where the parcel is in real time. Businesses have a hard time manually managing dispatching and routing. Clients often have trouble expecting the parcel.</p>
  <p class="body">Brantiq has developed an intelligent mobile ,web based logistics management software that gives management visibility to businesses over their own or third party fleets and awareness to customers about their parcel status. Brantiq automates the manual task of dispatching, routing, and tracking; optimizing and maximizing your fleet's productivity.</p>
</section>

<p class="tagline">Brantiq is the new rush. <strong>go brantiq!</strong></p>

<footer class="site-footer">
  <div class="footer-col col-company"><h3>Company</h3><ul><li>Support</li><li>Price</li><li>Sign up</li><li>Contact</li></ul></div>
  <div class="footer-col col-community"><h3>Community</h3><ul><li>Guiglines</li><li>Terms and conditions</li><li>privacy policy</li><li>site map</li></ul></div>
  <div class="footer-col col-follow"><h3>Follow us</h3><ul><li>Friendwall</li><li>Chirper</li><li>Snapframe</li><li>findly</li></ul></div>
  <div class="footer-col col-contact"><h3>Contact us</h3><ul><li>Address : 200 Latin words, combined with a handful</li><li>Ph : 5550142368 / 5550142368</li><li>E mail : hello@brantiq.example</li></ul></div>
  <div class="footer-col col-newsletter"><h3>Newsletter</h3></div>
  <div class="newsletter-input">Enter The Mail Id</div>
  <div class="newsletter-btn">Send Now</div>
</footer>
<div class="footer-bottom">Copyrights@2016Company name all rights reserved</div>
</body>
</html>
```